Coastal Learner Bureau business cards

Australian company about to start offering its services. We recruit international students to come to study English, vocational education and postgraduate courses in Australia. We help them find the institution and select the right city they want to come to Australia. We are a young, online oriented and supportive agency. Our clients are between 18 and 35 years old, mainly University students, young professionals or people with work experience. We provide much more information that any other agency offer. We administrate a Facebook group with more than 11.000 members that daily ask questions about general information when coming to Australia, while they are here and even after they leave the country

Target Market(s)

International students from South America, Central America and Europe

Industry/Entity Type

Student

Contact Information for Business Card

Tomas Bilbrea
Managing Director
tomas@kelvarin.com.au
www.kelvoria.com.au
+61 491058264
Melbourne, Australia

Font styles to use
Serif
Sans Serif

Colors

Designer to choose colors to be used in the design.

Requirements
Must have
• Horizontal design
• Standard business card size and shape. If font uses green or yellow colours, they will have to match the ones from the logo
Nice to have
• UPDATE: Use the contents of the green image to design one of the card sides. Use our logo in the background of that side as watermark.
• Passport image, or immigration stamps. A picture of the Yarra River (from Melbourne) would be cool as well.
Should not have
• Non-standard business card size and shape
• Not black as the background colour of any sides as we are not a VIP agency or a hight class service. We are orientes to young people and they like colours, pictures, something attractive.
• Vertical design
• NO YELLOW or BLACK AS THE BACKGROUND COLOUR OF ANY SIDE OF THE BIZ CARD

```html
<!DOCTYPE html>
<html lang="en">
<head>
<meta charset="utf-8">
<title>Kelvoria business cards</title>
<link rel="stylesheet" href="https://fonts.googleapis.com/css2?family=Source+Sans+3:wght@400;600;700&display=swap">
<style>
  :root {
    --canvas: #e9e6e1;
    --card: #f7f7f6;
    --green: #12653e;
    --green-light: #1a7a4b;
    --yellow: #efc31c;
    --ink: #3f3f3f;
    --rule: #8a8a8a;
    --white: #ffffff;
  }
  * { box-sizing: border-box; margin: 0; padding: 0; }
  html, body {
    width: 1200px; height: 886px; overflow: hidden;
    background: var(--canvas);
    font-family: "Source Sans 3", Arial, sans-serif;
  }
  .canvas { position: relative; width: 1200px; height: 886px; }
  .card {
    position: absolute; width: 600px; height: 343px;
    background: var(--card); border-radius: 20px; overflow: hidden;
    box-shadow: 0 6px 18px rgba(0,0,0,.18);
  }
  .card--front { left: 90px; top: 70px; }
  .card--back { left: 510px; top: 470px; }

  .brand {
    display: flex; align-items: center; gap: 10px;
    color: var(--green); font-weight: 700; letter-spacing: .5px;
  }
  .brand__dot { width: 18px; height: 18px; border-radius: 50%; background: var(--yellow); }
  .card--front .brand { position: absolute; left: 50%; top: 110px; transform: translateX(-50%); font-size: 58px; }
  .card--front .brand__dot { width: 22px; height: 22px; }

  .tagline {
    position: absolute; left: 70px; right: 70px; top: 232px;
    display: flex; align-items: center; gap: 12px;
    color: var(--ink); font-size: 15px; font-weight: 600;
  }
  .tagline::before, .tagline::after { content: ""; flex: 1; height: 1px; background: var(--rule); }

  .wave { position: absolute; inset: 0; width: 100%; height: 100%; }
  .card--back .brand { position: absolute; left: 50px; top: 120px; font-size: 50px; }

  .contact {
    position: absolute; right: 30px; top: 92px; text-align: right; color: var(--white);
  }
  .contact__name { color: var(--yellow); font-size: 22px; font-weight: 700; line-height: 1.1; }
  .contact__role { font-size: 16px; font-weight: 600; margin-bottom: 14px; margin-right: 26px; }
  .contact__list { list-style: none; }
  .contact__item {
    display: flex; align-items: center; justify-content: flex-end; gap: 8px;
    font-size: 14px; line-height: 24px;
  }
  .contact__icon { width: 16px; height: 16px; flex: none; }
</style>
</head>
<body>
<main class="canvas">

  <section class="card card--front" aria-label="Card front">
    <div class="brand"><span class="brand__dot"></span>Kelvoria</div>
    <p class="tagline">Hacemos más por ti!</p>
  </section>

  <section class="card card--back" aria-label="Card back">
    <svg class="wave" viewBox="0 0 600 343" preserveAspectRatio="none" aria-hidden="true">
      <path d="M478,0 H600 V343 H160 C200,312 280,300 330,286 C420,258 400,60 478,0 Z" fill="var(--green)"/>
      <path d="M464,0 C388,58 410,246 322,276 C270,292 200,296 150,318" fill="none" stroke="var(--white)" stroke-width="14"/>
      <path d="M458,0 C382,56 402,240 318,270 C266,286 196,290 146,312" fill="none" stroke="var(--yellow)" stroke-width="9"/>
    </svg>

    <div class="brand"><span class="brand__dot"></span>Kelvoria</div>

    <div class="contact">
      <p class="contact__name">Tomas Bilbrea</p>
      <p class="contact__role">Managing Director</p>
      <ul class="contact__list">
        <li class="contact__item">+61 491058264
          <svg class="contact__icon" viewBox="0 0 16 16"><circle cx="8" cy="8" r="8" fill="var(--yellow)"/><path d="M5 4.5c.6-.5 1.2-.4 1.5.2l.5 1c.2.5 0 .8-.4 1.1.4.9 1 1.6 1.9 2 .3-.4.7-.6 1.1-.4l1 .5c.6.3.7.9.2 1.5-.9 1-2.4.7-3.9-.6S4 5.5 5 4.5z" fill="var(--green)"/></svg>
        </li>
        <li class="contact__item">tomas@kelvarin.com.au
          <svg class="contact__icon" viewBox="0 0 16 16"><circle cx="8" cy="8" r="8" fill="var(--yellow)"/><rect x="4" y="5" width="8" height="6" rx="1" fill="var(--green)"/><path d="M4.3 5.4 8 8.3l3.7-2.9" fill="none" stroke="var(--yellow)" stroke-width=".9"/></svg>
        </li>
        <li class="contact__item">www.kelvoria.com.au
          <svg class="contact__icon" viewBox="0 0 16 16"><circle cx="8" cy="8" r="8" fill="var(--yellow)"/><circle cx="8" cy="8" r="4" fill="none" stroke="var(--green)" stroke-width="1.2"/><path d="M4 8h8M8 4c-1.6 2.4-1.6 5.6 0 8M8 4c1.6 2.4 1.6 5.6 0 8" fill="none" stroke="var(--green)" stroke-width="1"/></svg>
        </li>
        <li class="contact__item">Melbourne, Australia
          <svg class="contact__icon" viewBox="0 0 16 16"><circle cx="8" cy="8" r="8" fill="var(--yellow)"/><path d="M8 12.5S5 9.3 5 7a3 3 0 0 1 6 0c0 2.3-3 5.5-3 5.5z" fill="var(--green)"/><circle cx="8" cy="7" r="1.1" fill="var(--yellow)"/></svg>
        </li>
      </ul>
    </div>
  </section>

</main>
</body>
</html>
```